Varnex Consulting Business card design.

See our website www.varnexconsulting.example which will give you a good idea of what we are about. The font is called 'Play'.

I'd like a standout business card in keeping with the themes and branding on the website

Target Market(s)

professionals. HR directors

Industry/Entity Type

Business

Contact Information for Business Card

Varnex Consulting PO Box 3172 Merrowdale NSW 2291 1300 485 193 Gavin Threlkeld Principal email: career@varnexconsulting.example ABN: 71203948865

Font styles to use
Other font styles liked:
• Play

Requirements
Must have
• Must have same design colours and branding as website.
• On back I'd prefer a list of the things we do which appears below the name at the header on the website

```html
<!DOCTYPE html>
<html lang="en">
<head>
<meta charset="utf-8">
<title>Varnex Consulting – Business Card</title>
<link href="https://fonts.googleapis.com/css2?family=Play:wght@400;700&display=swap" rel="stylesheet">
<style>
  :root {
    --page: #e9ebee;
    --navy-deep: #0b2235;
    --navy: #163a55;
    --navy-mid: #23506f;
    --sky: #2bb5e6;
    --sky-light: #5fd0f3;
    --sky-dark: #1d7fb4;
    --white: #ffffff;
    --photo-warm: #b8898a;
    --photo-track: #8a4a40;
    --photo-dark: #2a2f3d;
  }
  * { margin: 0; padding: 0; box-sizing: border-box; }
  html, body { width: 1200px; height: 902px; overflow: hidden; }
  body {
    background: var(--page);
    font-family: 'Play', sans-serif;
    position: relative;
  }
  .card {
    position: absolute;
    width: 700px;
    height: 400px;
    overflow: hidden;
    border-radius: 4px;
    box-shadow: 0 10px 28px rgba(10, 30, 50, 0.28);
    background: linear-gradient(160deg, var(--navy-mid) 0%, var(--navy) 45%, var(--navy-deep) 100%);
  }
  .card--front { left: 150px; top: 34px; }
  .card--back  { left: 350px; top: 468px; }
  .card__art { position: absolute; inset: 0; width: 700px; height: 400px; }

  .brand {
    position: absolute;
    font-size: 42px;
    letter-spacing: 1px;
    white-space: nowrap;
    line-height: 1;
  }
  .brand__first { color: var(--white); }
  .brand__second { color: var(--sky); }
  .services {
    position: absolute;
    font-size: 13.5px;
    color: var(--sky);
    letter-spacing: 0.6px;
    white-space: nowrap;
  }
  .card--front .brand { left: 40px; top: 318px; }
  .card--front .services { left: 44px; top: 366px; }

  .card--back .brand { left: 40px; top: 78px; font-size: 46px; }
  .card--back .services { left: 44px; top: 130px; }
  .person { position: absolute; left: 44px; top: 218px; }
  .person__name { color: var(--sky); font-size: 30px; line-height: 1.1; }
  .person__role { color: var(--white); font-size: 22px; line-height: 1.2; }

  .contact {
    position: absolute;
    right: 30px;
    top: 206px;
    list-style: none;
    text-align: right;
    color: var(--white);
    font-size: 16px;
    line-height: 30px;
  }
  .contact li { display: flex; justify-content: flex-end; align-items: center; gap: 10px; white-space: nowrap; }
  .contact__abn { font-size: 19px; padding-right: 28px; }
  .contact__icon { width: 18px; height: 18px; flex: none; }
</style>
</head>
<body>

<section class="card card--front" aria-label="Card front">
  <svg class="card__art" viewBox="0 0 700 400">
    <defs>
      <linearGradient id="photoTone" x1="0" y1="0" x2="1" y2="1">
        <stop offset="0" stop-color="var(--photo-warm)"/>
        <stop offset="0.55" stop-color="var(--photo-track)"/>
        <stop offset="1" stop-color="var(--photo-dark)"/>
      </linearGradient>
    </defs>
    <path role="img" aria-label="Photo of sprinters' hands set on the starting line of a running track"
          d="M0,0 H700 V195 C540,188 390,290 170,306 C100,310 40,308 0,304 Z"
          fill="url(#photoTone)"/>
    <path d="M0,304 C40,308 100,310 170,306 C390,290 540,188 700,195"
          fill="none" stroke="var(--sky)" stroke-width="4"/>
  </svg>
  <div class="brand"><span class="brand__first">VARNEX</span> <span class="brand__second">CONSULTING</span></div>
  <div class="services">Search &amp; Select | Career | Coaching | Leadership | Outplacement</div>
</section>

<section class="card card--back" aria-label="Card back">
  <svg class="card__art" viewBox="0 0 700 400" aria-hidden="true">
    <defs>
      <linearGradient id="swoosh" x1="1" y1="0" x2="0.3" y2="1">
        <stop offset="0" stop-color="var(--sky-light)"/>
        <stop offset="0.5" stop-color="var(--sky)"/>
        <stop offset="1" stop-color="var(--sky-dark)"/>
      </linearGradient>
      <linearGradient id="gloss" x1="0" y1="0" x2="0" y2="1">
        <stop offset="0" stop-color="#ffffff" stop-opacity="0.12"/>
        <stop offset="1" stop-color="#ffffff" stop-opacity="0"/>
      </linearGradient>
    </defs>
    <path d="M0,0 H700 V40 C480,60 240,130 0,150 Z" fill="url(#gloss)"/>
    <path d="M700,30 C640,170 420,200 360,280 C320,330 300,370 290,400 H700 Z" fill="url(#swoosh)"/>
    <path d="M700,30 C640,170 420,200 360,280 C320,330 300,370 290,400"
          fill="none" stroke="var(--white)" stroke-width="5"/>
  </svg>
  <div class="brand"><span class="brand__first">VARNEX</span> <span class="brand__second">CONSULTING</span></div>
  <div class="services">Search &amp; Select | Career | Coaching | Leadership | Outplacement</div>
  <div class="person">
    <div class="person__name">Gavin Threlkeld</div>
    <div class="person__role">Principal</div>
  </div>
  <ul class="contact">
    <li class="contact__abn">ABN: 71203948865</li>
    <li>1300 485 193
      <svg class="contact__icon" viewBox="0 0 18 18"><rect width="18" height="18" rx="3" fill="var(--white)"/><path d="M5 4 L7.5 4 L8.5 7 L7 8 C7.8 9.8 8.7 10.8 10 11.2 L11 9.8 L14 10.8 L14 13 C9 14 4 9 5 4 Z" fill="var(--sky)"/></svg>
    </li>
    <li>career@varnexconsulting.example
      <svg class="contact__icon" viewBox="0 0 18 18"><rect width="18" height="18" rx="3" fill="var(--white)"/><rect x="3.5" y="5" width="11" height="8" fill="none" stroke="var(--sky)" stroke-width="1.5"/><path d="M3.5 5 L9 9.5 L14.5 5" fill="none" stroke="var(--sky)" stroke-width="1.5"/></svg>
    </li>
    <li>PO Box 3172 Merrowdale NSW 2291
      <svg class="contact__icon" viewBox="0 0 18 18"><rect width="18" height="18" rx="3" fill="var(--white)"/><path d="M9 15 C6 11 5 9 5 7.2 A4 4 0 0 1 13 7.2 C13 9 12 11 9 15 Z" fill="var(--sky)"/><circle cx="9" cy="7.2" r="1.5" fill="var(--white)"/></svg>
    </li>
  </ul>
</section>

</body>
</html>
```